Website Design for Wheels for Servicemen.org - Donated Cars to Disabled Vets

Need a Wordpress website. The coding now, esp. the CDONT coding is not supported by many hosting sites. Looking for a landing page to generate leads.

Logo Text

look at current one for ideas

Coding

Coded - Design and coding required

Number of Pages Required

1 page

Requirements
Must have
• look at current website at www.wheelsforservicemen.org
Nice to have
• look at this site: http://givevehicletoservicemen.org

```html
<!DOCTYPE html>
<html lang="en">
<head>
<meta charset="utf-8">
<title>Wheels for Servicemen.org – Donate Your Car</title>
<link rel="stylesheet" href="https://fonts.googleapis.com/css2?family=Raleway:wght@300;400;500;600;700&display=swap">
<style>
:root{
  --blue:#2460b3;
  --blue-dark:#123a78;
  --blue-text:#2a6db3;
  --red:#a3150f;
  --red-dark:#8a100b;
  --ink:#333;
  --muted:#8a8a8a;
  --light:#f6f6f6;
  --white:#fff;
}
*{margin:0;padding:0;box-sizing:border-box}
html,body{width:726px;height:1200px;overflow:hidden;background:var(--white)}
body{position:relative;font-family:'Raleway',sans-serif;color:var(--ink)}
.abs{position:absolute}

/* header */
.site-header{left:0;top:0;width:726px;height:46px;background:linear-gradient(180deg,#2d69bd,#1f56a9)}
.brand{left:110px;top:13px;display:flex;align-items:center;gap:6px;color:var(--white);font-size:14px;font-weight:500}
.brand-mark{width:14px;height:14px;background:var(--red);border:1px solid var(--white)}
.hotline{left:484px;top:11px;display:flex;align-items:center;gap:8px;color:var(--white)}
.hotline-text{text-align:center}
.hotline-label{font-size:5.5px}
.hotline-number{font-size:13px;font-weight:500;line-height:1.1}

/* hero */
.hero{left:0;top:46px;width:726px;height:293px;background:linear-gradient(90deg,#16356f 0%,#1d4f98 45%,#2456a6 65%,#6c88b9 82%,#b84a55 100%)}
.hero-title{left:119px;top:140px;font-size:22px;font-weight:300;color:var(--white)}
.hero-copy{left:120px;top:176px;width:215px;font-size:7px;line-height:13px;color:#d7e0ef}
.btn{display:flex;align-items:center;justify-content:center;background:var(--red);color:var(--white);text-transform:uppercase}
.btn-hero{left:120px;top:218px;width:104px;height:27px;font-size:7.5px;font-weight:500}
.slider-dots{left:124px;top:270px;display:flex;gap:8px}
.slider-dots span{width:5px;height:5px;border-radius:50%;background:var(--white)}
.slider-dots span.active{background:var(--red)}

.donate-form{left:423px;top:73px;width:178px;height:244px;background:rgba(14,45,104,.88)}
.donate-form h2{position:absolute;left:13px;top:22px;font-size:10px;font-weight:400;color:var(--white)}
.field{position:absolute;left:13px;width:152px;height:15px;border:1px solid #8ea6d2;font-size:5px;color:#e3e9f5;padding:0 7px;display:flex;align-items:center;justify-content:space-between}
.btn-form{position:absolute;left:13px;top:208px;width:64px;height:19px;font-size:5.5px;font-weight:700}

/* features */
.features{left:0;top:339px;width:726px;height:213px}
.feature{position:absolute;top:44px;display:flex;gap:10px}
.feature h3{font-size:7px;font-weight:700;color:#222;margin-bottom:6px}
.feature p{font-size:7px;line-height:13.5px;color:var(--muted);width:100px}
.btn-main{width:161px;height:31px;font-size:10px;font-weight:700;border-radius:2px}
.features .btn-main{left:278px;top:127px}
.features-note{left:0;top:165px;width:726px;text-align:center;font-size:7px;color:#555}

/* why */
.why{left:0;top:552px;width:726px;height:280px;background:var(--light)}
.why h2{position:absolute;left:0;top:33px;width:726px;text-align:center;font-size:15px;font-weight:400;color:var(--blue-text)}
.why-card{position:absolute;top:80px;width:153px}
.why-photo{width:153px;height:92px;border-radius:2px}
.why-card h3{margin-top:21px;font-size:7px;font-weight:400;color:var(--blue-text)}
.why-card p{margin-top:12px;font-size:7px;line-height:13.5px;color:var(--muted)}

/* cta banner */
.cta{left:0;top:832px;width:726px;height:292px;background:linear-gradient(90deg,#3a3a3a 0%,#5a5a5a 35%,#8d8d8d 60%,#bdbdbd 80%,#6e6e6e 100%)}
.cta h2{position:absolute;left:103px;top:80px;font-size:15px;font-weight:400;color:var(--white)}
.cta ul{position:absolute;left:105px;top:118px;list-style:none}
.cta li{display:flex;align-items:center;gap:10px;height:19px;font-size:8px;color:#e6e6e6}
.cta .btn-main{left:104px;top:221px}

/* footer */
.site-footer{left:0;top:1124px;width:726px;height:76px;background:var(--white)}
.copyright{left:124px;top:36px;font-size:5.5px;color:#333}
.policy{left:272px;top:36px;font-size:5.5px;color:#333}
.badge{top:26px;background:#d9d9d9}
.badge-a{left:428px;width:38px;height:29px}
.badge-b{left:492px;width:112px;height:28px;border-radius:3px}
.footer-code{left:700px;top:36px;font-size:5.5px;color:#333}
</style>
</head>
<body>

<header class="site-header abs">
  <div class="brand abs"><span class="brand-mark"></span>Wheels for Servicemen</div>
  <div class="hotline abs">
    <svg width="22" height="22" viewBox="0 0 24 24" fill="none" stroke="#fff" stroke-width="1.3"><path d="M5 3h4l2 5-2.5 1.5a11 11 0 0 0 6 6L16 13l5 2v4a2 2 0 0 1-2 2A17 17 0 0 1 3 5a2 2 0 0 1 2-2z"/><path d="M15 3a6 6 0 0 1 6 6M15 6a3 3 0 0 1 3 3"/></svg>
    <div class="hotline-text">
      <div class="hotline-label">We Need Your Help ?</div>
      <div class="hotline-number">1-800-555-0142</div>
    </div>
  </div>
</header>

<section class="hero abs" role="img" aria-label="Soldier in dress uniform beside a waving American flag">
</section>
<h1 class="hero-title abs">Wheels For Servicemen</h1>
<p class="hero-copy abs">Neque porro quisquam est qui dolorem ipsum quia dolor sit amet, consectetur, adipisci velit...</p>
<a class="btn btn-hero abs">Read More</a>
<div class="slider-dots abs"><span class="active"></span><span></span><span></span><span></span></div>

<form class="donate-form abs">
  <h2>DONATE HERE</h2>
  <div class="field" style="top:47px">Name</div>
  <div class="field" style="top:66px">Phone Number</div>
  <div class="field" style="top:85px">Address</div>
  <div class="field" style="top:104px">State <svg width="6" height="4" viewBox="0 0 6 4"><path d="M0 0l3 3 3-3" stroke="#fff" fill="none"/></svg></div>
  <div class="field" style="top:123px">E-mail</div>
  <div class="field" style="top:143px">Cell Phone</div>
  <div class="field" style="top:161px">City</div>
  <div class="field" style="top:181px">Zip Code</div>
  <a class="btn btn-form">Donate Now</a>
</form>

<section class="features abs">
  <div class="feature" style="left:125px">
    <svg width="36" height="36" viewBox="0 0 36 36"><path d="M3 10h5l2 6-3 2a14 14 0 0 0 8 8l2-3 6 2v5a2 2 0 0 1-2 2A23 23 0 0 1 1 12a2 2 0 0 1 2-2z" fill="#1d5eb3"/><ellipse cx="24" cy="8" rx="10" ry="7" fill="#1d5eb3"/><path d="M18 13l-2 5 6-3z" fill="#1d5eb3"/><circle cx="20" cy="8" r="1.3" fill="#fff"/><circle cx="24" cy="8" r="1.3" fill="#fff"/><circle cx="28" cy="8" r="1.3" fill="#fff"/></svg>
    <div><h3>HELP LINE</h3><p>Neque porro quisquam est qui dolorem ipsum quia dolor sit amet ...</p></div>
  </div>
  <div class="feature" style="left:288px">
    <svg width="48" height="30" viewBox="0 0 48 30"><path d="M2 14h8l3-7h10v14H2z" fill="#1d5eb3"/><rect x="23" y="15" width="18" height="6" fill="#1d5eb3"/><path d="M30 15l12-13 2 2-10 11" fill="#1d5eb3"/><circle cx="9" cy="23" r="4" fill="#1d5eb3" stroke="#fff" stroke-width="1.5"/><circle cx="33" cy="23" r="4" fill="#1d5eb3" stroke="#fff" stroke-width="1.5"/><rect x="13" y="9" width="6" height="4" fill="#fff"/></svg>
    <div><h3>WE TOW IT</h3><p>Neque porro quisquam est qui dolorem ipsum quia dolor sit amet ...</p></div>
  </div>
  <div class="feature" style="left:452px">
    <svg width="30" height="40" viewBox="0 0 30 40"><rect x="1" y="1" width="28" height="38" rx="3" fill="none" stroke="#1d5eb3" stroke-width="2"/><rect x="5" y="5" width="20" height="7" fill="#1d5eb3"/><g fill="#1d5eb3"><rect x="5" y="15" width="5" height="4"/><rect x="12" y="15" width="5" height="4"/><rect x="19" y="15" width="6" height="4"/><rect x="5" y="21" width="5" height="4"/><rect x="12" y="21" width="5" height="4"/><rect x="19" y="21" width="6" height="4"/><rect x="5" y="27" width="5" height="4"/><rect x="12" y="27" width="5" height="4"/><rect x="19" y="27" width="6" height="4"/></g></svg>
    <div><h3>TAX WRITE OFF</h3><p>Neque porro quisquam est qui dolorem ipsum quia dolor sit amet ...</p></div>
  </div>
  <a class="btn btn-main abs">Donate Your Car</a>
  <p class="features-note abs">Full Tax Deduction -Running or not</p>
</section>

<section class="why abs">
  <h2>Why Donate Your Car To Us ?</h2>
  <div class="why-card" style="left:122px">
    <div class="why-photo" role="img" aria-label="Hand giving a thumbs up" style="background:linear-gradient(90deg,#8fb6c9,#a9c7d3)"></div>
    <h3>IRS 501(C)3 Approved</h3>
    <p>Neque porro quisquam est qui dolorem ipsum quia dolor sit amet, consectetur...</p>
  </div>
  <div class="why-card" style="left:287px">
    <div class="why-photo" role="img" aria-label="Tow truck lifting a red car" style="background:linear-gradient(180deg,#b9b4a8,#8a7a64 60%,#c9a53a)"></div>
    <h3>Free Local Towing To You</h3>
    <p>Neque porro quisquam est qui dolorem ipsum quia dolor sit amet, consectetur...</p>
  </div>
  <div class="why-card" style="left:452px">
    <div class="why-photo" role="img" aria-label="Vintage cars in a showroom" style="background:linear-gradient(180deg,#5b3a26,#8a6a4e 50%,#3a2a20)"></div>
    <h3>All Cars Accepted</h3>
    <p>Neque porro quisquam est qui dolorem ipsum quia dolor sit amet, consectetur...</p>
  </div>
</section>

<section class="cta abs" role="img" aria-label="Black and white portrait of a servicewoman in uniform cap looking upward">
  <h2>Donate Your Car Today !</h2>
  <ul>
    <li><svg width="9" height="9" viewBox="0 0 10 10" fill="none" stroke="#e6e6e6"><rect x="0.5" y="1.5" width="8" height="8"/><path d="M2 5l2 2 5-6"/></svg>You have no costs</li>
    <li><svg width="9" height="9" viewBox="0 0 10 10" fill="none" stroke="#e6e6e6"><rect x="0.5" y="1.5" width="8" height="8"/><path d="M2 5l2 2 5-6"/></svg>Free Towing running or not</li>
    <li><svg width="9" height="9" viewBox="0 0 10 10" fill="none" stroke="#e6e6e6"><rect x="0.5" y="1.5" width="8" height="8"/><path d="M2 5l2 2 5-6"/></svg>We issue you an IRS tax receipt</li>
    <li><svg width="9" height="9" viewBox="0 0 10 10" fill="none" stroke="#e6e6e6"><rect x="0.5" y="1.5" width="8" height="8"/><path d="M2 5l2 2 5-6"/></svg>We take care of all paperwork</li>
    <li><svg width="9" height="9" viewBox="0 0 10 10" fill="none" stroke="#e6e6e6"><rect x="0.5" y="1.5" width="8" height="8"/><path d="M2 5l2 2 5-6"/></svg>We take care of DMV &amp; Smog issues</li>
  </ul>
  <a class="btn btn-main abs">Donate Your Car</a>
</section>

<footer class="site-footer abs">
  <p class="copyright abs">© 2016 Company Name | All Rights Reserved</p>
  <p class="policy abs">Privacy Policy</p>
  <div class="badge badge-a abs" aria-label="Partner badge"></div>
  <div class="badge badge-b abs" aria-label="Security badge"></div>
  <p class="footer-code abs">C5</p>
</footer>

</body>
</html>
```